Nutritional & Gastrointestinal Health Consulting Service-Website design

We need a website design for a new health consulting service called "Bright Vale" based in Perth, Australia.

We will be providing consulting services in the areas of:
1) Nutrition and Diet
2) Gastrointestinal Health (which means stomach & digestive system related health)

These consulting services will be provided by an Accredited Dietitian and a Paediatric Gastroenterologist.

We are open to creative ideas in terms of design, layout, fonts and colours. We also would love to see images of nature in the backdrop with families (adults with kids) having a good time, fresh fruits and vegetables displayed in a farmer's market or supermarket. 2 or 3 images should be sufficient. We would also definitely want our logo somewhere in the main page of website. The logo file is also attached. Please have a look at a website's design that we really liked. We would love to see designs inspired by that style. The website details are in the in the "nice to have priorities" section of this project brief.

We also would be looking at website designers with software coding skills so that if we like the design we can go ahead with the next step of coding.

The website design should communicate the purpose of the website and at the same time be simple, elegant and unique/eye-catching.

We look forward to receiving creative ideas for our website from you all. Good luck!

More details have been added to our project- for example: Logo, fonts style, must haves etc etc. Please view the updated project brief. Looking forward to receiving your fantastic ideas for our website. Thanking you

Hi, I have updated the colour preference. Will add the content preferences tomorrow. thanks

Hello all, I have now added a LOT more content to what we want in our website. It is very much in detail, so please carefully have a read through the entire project brief. If you have any questions write back to me and I will try to respond as quickly as I can. Last few days were busy so couldn't respond quickly to all of you who had send me designs/queries/questions. Thank you for your patience. I look forward to receiving fantastic designs from you all. Good Luck :-)

Target Market(s)

Adults based in western speaking countries aged 18 to 60 years

Industry/Entity Type

Software

Font styles to use
Sans Serif
Script

Colors
faa54b
acd036

Requirements
Must have
• The website must have the MAIN logo file attached. I have attached 3 files: 1) MAIN logo; 2) supplementary logo A ; 3) supplementary logo B

I have selected 2 colours from the colour scheme (see below)-(as the colour of our logo is that).
However we would also like to see LIGHT CHOCOLATE BROWN or CHOCOLATE BROWN colour used as the background colour of the website
Preferred WEBSITE CONTENT:
1) HOME PAGE:
Content required=
--Company Logo
--Dr Dorian Pelham
Paediatric Gastroenterologist & Hepatologist
-Marla Pelham.
Dietitian & Nutritionist
--Website Menu (either listed horizontally or vertically):
Once clicked on each name:

Under each of the Website Menu items we want the following Headings to be added

2) ABOUT US page:
Sub-heading under this: Qualification, Skills, Special Interest

3) SERVICES
DORIAN'S PAGE: Individual Consultation, Endoscopy procedures
Individual Consultation, Group Based Services, Food Diary, Food & Symptom Diary

4) FEES & REBATE: Content as below:
Please Note: Payment of full fees is required at the time of consultation and procedures. 48 hours notice is required for cancellation of appointments/non-attendance. Failure to provide this may result in a fee being incurred. Please call reception to find out the amount of fee charged for cancellation of appointments/non-attendance.
headings are:
Paediatric Gastroenterology:
Dorian's pge
Individual Consultation - Initial (upto 30 mins):
Review Consultation (upto 15 mins):
Endoscopy procedures - No Gap fees charged. Fees will be billed directly to Vitacover. If any queries, please contact reception.

marla's pge
sub heading:
Individual Consultation - Initial (upto 45 mins):
Individual Consultation - Review (upto 30 mins):

Concession-Individual Consultation -Initial (upto 45 mins):
Concession-Individual Consultation - Review (upto 30 mins):
Please Note: Concession applies for health care card holders & pensioners

Group Based Services: Pricing subject to the type of service provided. Please contact us for an obligation free quote.
Education Topics Include:
- Paediatric Nutrition (Introducing Solids, Fussy Eating, Healthy Eating)
- Pregnancy Nutrition, Gestational Diabetes, Breastfeeding/Lactation Nutrition
- Healthy Eating, Supermarket Shopping Tips, Nutrition Label Reading Tips, Healthier
sub heading under nutrition & diet:
-Vitacover:
--A rebate of $52.95 is available from Vitacover if an EPC ( Enhanced Primary Care)/Chronic Disease Management (CDM) plan is issued by your GP.
--All mandatory paperwork needs to be available at the time of making your appointment for your eligibility.
-Private Health Fund:
--Most private health funds provide rebate on dietetic appointments. However the rebate amount depends on your level of cover. Thus, please contact your health fund to determine your entitled rebate.
-RSB: Approved provider for RSB services

6) FOR DOCTORS: Bright Vale Paediatric Gastroenterologist Referral Form
Bright Vale Dietitian Referral form
7) LOCATIONS & CONTACT

Paediatric Gastroenterology & Hepatology Service
Suite 46
Holy Lantern Bramcote Medical Centre
17 Colin Ferris Pde,
MURDOCH, WA 6150
P: (08) 9422 5061
F: (08) 9422 3094

Nutrition & Diet Service
Suite 46
17 Colin Ferris Pde,
MURDOCH, WA 6150
P: (08) 9422 5061
F: (08) 9422 3094

Tolland Medical Centre
58-60 Karrigan Parkway,
MANDURAH, WA 6210
P: (08) 9647 2283
F: (08) 96724419
www.tmcexample.com.au

This page should have a webform that has following titles:
-Your Name
-Your Email
-Your Phone
-Message

8) NEWS & BLOG
Nice to have
• We liked the design style of the websites below:
https://www.vendoraplex.example/

http://qoravelt.example/

But feel free to use your creativity too
Should not have
• Please do not use any body building or muscle building images

```html
<!DOCTYPE html>
<html lang="en">
<head>
<meta charset="utf-8">
<title>Bright Vale – For Patients</title>
<link rel="stylesheet" href="https://fonts.googleapis.com/css2?family=Open+Sans:wght@300;400;600;700&display=swap">
<style>
  :root {
    --page-orange: #faa54b;
    --field-orange: #e3933f;
    --tab-orange: #e69a46;
    --ink-dark: #3b2a24;
    --ink-brown: #4a2a1e;
    --ink-rust: #7f3a12;
    --line-light: #fde2c0;
    --white: #ffffff;
    --button-shadow: #d6d6d6;
  }
  * { box-sizing: border-box; margin: 0; padding: 0; }
  html, body { width: 1200px; height: 832px; overflow: hidden; }
  body {
    position: relative;
    background: var(--page-orange);
    font-family: "Open Sans", Arial, sans-serif;
    color: var(--ink-dark);
  }
  .side-tab {
    position: absolute; top: 89px; width: 47px; height: 47px;
    background: var(--tab-orange);
    display: flex; align-items: center; justify-content: center;
    color: var(--white);
  }
  .side-tab--menu { left: 0; }
  .side-tab--close { right: 0; font-size: 13px; }
  .page-title {
    position: absolute; top: 87px; left: 0; width: 100%;
    text-align: center; color: var(--white);
    font-weight: 700; font-size: 16px; letter-spacing: 0.2px;
  }
  .divider {
    position: absolute; top: 169px; left: 52px; width: 1094px;
    border-top: 1px dashed var(--line-light);
  }
  .section-badge {
    position: absolute; top: 216px; left: 441px; width: 318px; height: 75px;
    border: 1px solid var(--line-light);
    display: flex; align-items: center; justify-content: center;
    font-weight: 300; font-size: 37px; color: var(--ink-brown);
  }
  .intro {
    position: absolute; top: 304px; left: 0; width: 100%;
    text-align: center; font-weight: 300; font-size: 20.5px; line-height: 29px;
    color: var(--ink-dark);
  }
  .intro strong { font-weight: 600; }
  .form-title {
    position: absolute; top: 378px; left: 0; width: 100%;
    text-align: center; font-weight: 300; font-size: 32px; color: var(--ink-brown);
  }
  .appointment-form {
    position: absolute; top: 436px; left: 52px; width: 1096px; height: 47px;
    display: flex; gap: 10px;
  }
  .field {
    width: 290px; height: 47px; background: var(--field-orange);
    border: none; padding: 0 14px; position: relative;
    font-family: inherit; font-weight: 300; font-size: 13px;
    color: rgba(255,255,255,0.85);
    display: flex; align-items: center;
  }
  .field__grip { position: absolute; right: 2px; bottom: 2px; }
  .submit-button {
    width: 196px; height: 47px; background: var(--white);
    border: none; border-bottom: 4px solid var(--button-shadow);
    font-family: inherit; font-weight: 300; font-size: 17.5px; color: var(--ink-dark);
  }
  .info-column {
    position: absolute; top: 527px; width: 534px; text-align: center;
  }
  .info-column--education { left: 52px; }
  .info-column--information { left: 614px; }
  .info-column h3 {
    font-weight: 300; font-size: 17px; color: var(--ink-rust); margin-bottom: 14px;
  }
  .info-column p {
    font-family: Arial, "Helvetica Neue", sans-serif; font-size: 13.2px;
    line-height: 18.8px; color: var(--ink-dark);
  }
</style>
</head>
<body>
  <div class="side-tab side-tab--menu" aria-label="Menu">
    <svg width="12" height="10" viewBox="0 0 12 10" aria-hidden="true">
      <rect y="0" width="12" height="2" fill="#fff"/>
      <rect y="4" width="12" height="2" fill="#fff"/>
      <rect y="8" width="12" height="2" fill="#fff"/>
    </svg>
  </div>
  <div class="side-tab side-tab--close" aria-label="Close">×</div>

  <h1 class="page-title">FOR PATIENTS</h1>
  <div class="divider"></div>

  <h2 class="section-badge">CONSULTING</h2>
  <p class="intro">
    Lorem ipsum dolor sit amet, <strong>consectetuer</strong> adipiscing elit.<br>
    Sed diam <strong>nonummy nibh</strong> euismod tincidunt ut laoreet dolore magna aliquam erat volutpat.
  </p>

  <h2 class="form-title">APPOINMENT</h2>
  <form class="appointment-form">
    <div class="field">Name</div>
    <div class="field">Mail</div>
    <div class="field">Message
      <svg class="field__grip" width="10" height="10" viewBox="0 0 10 10" aria-hidden="true">
        <path d="M9 1L1 9M9 4L4 9M9 7L7 9" stroke="#fff" stroke-width="1" opacity="0.8"/>
      </svg>
    </div>
    <button class="submit-button" type="button">Make Appointment</button>
  </form>

  <section class="info-column info-column--education">
    <h3>EDUCATION</h3>
    <p>Lorem ipsum dolor sit amet, consectetuer, sed diam nonummy nibh euismod tincidunt ut laoreet dolore magna aliquam erat volutpat. Ut wisi enim ad minim veniam, quis nostrud exerci tation ullamcorper suscipit lobortis nisl ut aliquip ex ea <strong>commodo consequat</strong>. Duis autem vel eum iriure dolor in hendrerit in vulputate velit esse molestie consequat.</p>
  </section>
  <section class="info-column info-column--information">
    <h3>INFORMATION</h3>
    <p>Lorem ipsum dolor sit amet, consectetuer, sed diam nonummy nibh euismod tincidunt ut laoreet dolore magna aliquam erat volutpat. Ut wisi enim ad minim veniam, quis nostrud exerci tation ullamcorper suscipit lobortis nisl ut aliquip ex ea <strong>commodo consequat</strong>. Duis autem vel eum iriure dolor in hendrerit in vulputate velit esse molestie consequat.</p>
  </section>
</body>
</html>
```